Local massage therapist needs some new marketing material

Hi there! I am a massage therapist here in Denver, CO in Alder Bend(shopping and art district) of the city. My business is called Lumo Bodywork of Denver. My practice has an eastern influence and I do reflexology, thai massage and use Chinese herbs, etc. I know all my clients and pay close attention to details. I am also very respectful of tradition and it shows in how I work. I tend to like modern, clean, fun, Asian designs. I am wanting a new business card and brochure. I have a logo and branding for my business that I want used in the design. Currently, the sign for my building is purple and I think my logo was designed to be purple. I will attach pictures of it and can send whatever files are necessary so it can be integrated into the brochure, etc. I like the purple but open to using other colors as well. Thanks!
My website is lumobodyworkofdenver.example where info can be gathered about me and services/fees for brochure.
Updates

Just increased budget. Please see new feedback in discussion thread.

Thanks!

                                       HEY ALL,

Just wanted to let you know that I made a change to my website. It is on the Prices Page. I no longer have the frequent  flyer prices but I added discounts. Let me know if you have any questions. Thanks so much!

Target Market(s)

healthy, urban, educated, upper middle class, yogis

Industry/Entity Type

Marketing

Requirements
Must have
• logo stays purple
Should not have
• not too busy

```html
<!DOCTYPE html>
<html lang="en">
<head>
<meta charset="utf-8">
<title>Lumo Bodywork of Denver – Business Card</title>
<link href="https://fonts.googleapis.com/css2?family=Open+Sans:ital,wght@0,400;0,600;0,700;1,400&display=swap" rel="stylesheet">
<style>
  :root {
    --purple: #6a2e91;
    --ink: #555459;
    --rule: #8c8b90;
    --card: #ffffff;
    --backdrop: #ece9ef;
    --faint: #eeedf1;
  }
  * { box-sizing: border-box; margin: 0; padding: 0; }
  html, body { width: 1200px; height: 720px; overflow: hidden; }
  body {
    background: var(--backdrop);
    font-family: "Open Sans", Arial, sans-serif;
    color: var(--ink);
  }
  .canvas {
    position: relative;
    width: 1200px;
    height: 720px;
    display: flex;
    align-items: center;
    justify-content: center;
    gap: 40px;
  }
  .card {
    position: relative;
    width: 540px;
    height: 309px;
    background: var(--card);
    box-shadow: 0 6px 18px rgba(60, 40, 80, 0.15);
    overflow: hidden;
  }

  /* Front */
  .front-decor {
    position: absolute;
    left: 150px;
    top: 34px;
    width: 200px;
    height: 240px;
    border-radius: 50%;
    background: radial-gradient(circle, var(--faint) 0%, rgba(238,237,241,0) 70%);
  }
  .identity {
    position: absolute;
    right: 320px;
    top: 102px;
    text-align: right;
    font-size: 14px;
    line-height: 20px;
    white-space: nowrap;
  }
  .identity .person-name {
    color: var(--purple);
    font-weight: 700;
    font-size: 19px;
    line-height: 25px;
  }
  .divider {
    position: absolute;
    left: 232px;
    top: 96px;
    width: 1px;
    height: 72px;
    background: var(--rule);
  }
  .contacts {
    position: absolute;
    left: 244px;
    top: 93px;
    list-style: none;
    font-size: 13px;
    line-height: 25px;
  }
  .contacts li { display: flex; align-items: center; gap: 6px; white-space: nowrap; }
  .contacts svg { width: 12px; height: 12px; flex: none; }

  /* Back */
  .brand {
    position: absolute;
    right: 34px;
    top: 26px;
    display: flex;
    flex-direction: column;
    align-items: center;
    gap: 10px;
  }
  .brand-dot {
    width: 46px;
    height: 46px;
    border-radius: 50%;
    background: var(--purple);
  }
  .brand-name {
    color: var(--purple);
    font-weight: 600;
    font-size: 30px;
    letter-spacing: 4px;
    line-height: 1;
  }
  .appointment {
    position: absolute;
    left: 40px;
    top: 110px;
    right: 34px;
  }
  .appointment-title {
    color: var(--purple);
    font-weight: 700;
    font-size: 14px;
    letter-spacing: 0.2px;
    margin-bottom: 18px;
  }
  .field-row {
    display: flex;
    align-items: flex-end;
    font-size: 14px;
    margin-bottom: 14px;
  }
  .field-line {
    border-bottom: 1px solid var(--rule);
    height: 14px;
    margin: 0 8px 3px;
  }
  .hours {
    font-size: 14px;
    line-height: 21px;
    margin-top: 6px;
  }
  .policy {
    font-style: italic;
    font-size: 14px;
    margin-top: 12px;
  }
</style>
</head>
<body>
<main class="canvas">

  <section class="card card-front">
    <div class="front-decor" role="img" aria-label="Faint lotus ornament watermark"></div>
    <div class="identity">
      <p class="person-name">Your Name</p>
      <p>Title</p>
      <p>1480 E Alder Ave, Denver</p>
      <p>CO 80206</p>
    </div>
    <div class="divider"></div>
    <ul class="contacts">
      <li>
        <svg viewBox="0 0 16 16" aria-hidden="true"><path fill="var(--ink)" d="M4 1l2.5 3-1.5 1.8c.8 2 2.3 3.5 4.2 4.2L11 8.5l3 2.5-1.5 3C7 14 2 9 2 2.5z"/></svg>
        303.555.0147
      </li>
      <li>
        <svg viewBox="0 0 16 16" aria-hidden="true"><rect x="1" y="3" width="14" height="10" rx="1" fill="var(--ink)"/><path d="M1.5 4l6.5 5 6.5-5" stroke="#fff" stroke-width="1.4" fill="none"/></svg>
        info@lumobodyworkofdenver.example
      </li>
      <li>
        <svg viewBox="0 0 16 16" aria-hidden="true"><circle cx="8" cy="8" r="6.5" fill="none" stroke="var(--ink)" stroke-width="1.4"/><ellipse cx="8" cy="8" rx="2.8" ry="6.5" fill="none" stroke="var(--ink)" stroke-width="1.2"/><path d="M1.5 8h13" stroke="var(--ink)" stroke-width="1.2"/></svg>
        www.lumobodyworkofdenver.example
      </li>
    </ul>
  </section>

  <section class="card card-back">
    <div class="brand">
      <span class="brand-dot"></span>
      <span class="brand-name">LUMO</span>
    </div>
    <div class="appointment">
      <h2 class="appointment-title">YOUR APPOINTMENT</h2>
      <div class="field-row">
        <span>Name :</span><span class="field-line" style="width:130px"></span>
        <span>Time :</span><span class="field-line" style="width:100px"></span>
        <span>am / pm</span>
      </div>
      <div class="field-row">
        <span>Date :</span><span class="field-line" style="width:110px"></span>
      </div>
      <p class="hours">Tues - Fri 10am - 8pm Sat 10am-5pm<br>(Appointments required) No walk-ins please.</p>
      <p class="policy">We appreciate a 24 hr. notice for cancellations</p>
    </div>
  </section>

</main>
</body>
</html>
```